Delia Marsh Catalog to submit to vendors

We need a catalog made with all of the products in our shop for sales purposes. Our Website is www.deliamarshandcompany.example
Almost all of our products are listed on the website. If you can not take the pictures from the site I can upload them. The descriptions are listed as well. There are three additional products that I will upload. This Catalog will be mailed to stores and should include MSRP Prices.
Updates

Hello There-We are looking for a sales catalog to send to stores in our area. We would like to include MSRP and the end we can add wholesale pricing with minimum orders. Our website is www.deliamarshandcompany.example. There are a few products that haven't been added to the website yet. Where can I upload them and send descriptions?Thank you,Colette Added Thursday, January 21, 2016

Target Market(s)

boutiques and gift shops

Industry/Entity Type

Shop

Font styles to use
Serif
Other font styles liked:
• Noteworthy

Colors
e34297
a64599
6b449b
0255a3

Requirements
Must have
• Color! I would like to organize the catalog by sections. Our premade section and our DIY kits. Maybe we should include Gift sets and put the baskets and gift boxes in one section

```html
<!DOCTYPE html>
<html lang="en">
<head>
<meta charset="utf-8">
<title>Delia Marsh – Pre-Made Collection</title>
<link rel="stylesheet" href="https://fonts.googleapis.com/css2?family=Itim&display=swap">
<style>
  :root {
    --pink: #e34297;
    --purple: #6b449b;
    --frame: #e04a9a;
    --paper: #ffffff;
    --backdrop: #e9e8ec;
  }
  html, body {
    margin: 0;
    padding: 0;
    width: 1200px;
    height: 1000px;
    overflow: hidden;
    background: var(--backdrop);
    font-family: "Itim", "Comic Sans MS", cursive;
  }
  .spread {
    position: absolute;
    left: 10px;
    top: 237px;
    width: 1180px;
    height: 413px;
    background: var(--paper);
    box-shadow: 0 3px 8px rgba(0,0,0,0.35);
  }
  .fold-band {
    position: absolute;
    left: 0;
    bottom: 0;
    width: 100%;
    height: 23px;
    background: var(--pink);
  }
  .page-header {
    position: absolute;
    top: 13px;
    height: 48px;
    background: var(--pink);
    border-radius: 24px;
    color: #fff;
  }
  .page-header.left { left: 25px; width: 543px; }
  .page-header.right { left: 610px; width: 540px; }
  .page-header h2 {
    margin: 0;
    font-weight: 400;
    font-size: 34px;
    line-height: 48px;
    text-align: center;
  }
  .page-number {
    position: absolute;
    top: 0;
    font-size: 18px;
    line-height: 48px;
  }
  .left .page-number { left: 16px; }
  .right .page-number { right: 12px; }
  .bubble-tail {
    position: absolute;
    bottom: -12px;
    right: 18px;
    width: 22px;
    height: 16px;
  }
  .product-photo {
    position: absolute;
    width: 155px;
    height: 112px;
    border: 6px solid var(--frame);
    border-radius: 14px;
    box-sizing: content-box;
  }
  .label {
    position: absolute;
    text-align: center;
    transform: translateX(-50%);
    white-space: nowrap;
    line-height: 21px;
  }
  .label .name { color: var(--pink); font-size: 15px; display: block; }
  .label .price { color: var(--purple); font-size: 17px; display: block; }
</style>
</head>
<body>
<main class="spread">

  <section class="page page-5">
    <header class="page-header left">
      <span class="page-number">5</span>
      <h2>Pre-Made Collection</h2>
      <svg class="bubble-tail" viewBox="0 0 22 16"><path d="M0 0 L22 0 L20 16 Z" fill="#e34297"/></svg>
    </header>

    <div class="product-photo" style="left:40px;top:76px;background:linear-gradient(135deg,#c8569f,#b84a98)" role="img" aria-label="Lip balm trio in a clear case"></div>
    <div class="product-photo" style="left:185px;top:139px;background:linear-gradient(135deg,#c44f9c,#a83f8c)" role="img" aria-label="Stacked single lip balm jars"></div>
    <div class="product-photo" style="left:262px;top:250px;background:linear-gradient(135deg,#d24a9f,#b83d8f)" role="img" aria-label="Three pump bottles of body lotion"></div>
    <div class="product-photo" style="left:385px;top:76px;background:linear-gradient(135deg,#c64d9d,#e8e4c8 60%,#b9449a)" role="img" aria-label="Open jar of body butter"></div>

    <div class="label" style="left:117px;top:203px"><span class="name">Lip Balm Trio</span><span class="price">from $14.00</span></div>
    <div class="label" style="left:202px;top:267px"><span class="name">Single Lip Balm</span><span class="price">from $5.00</span></div>
    <div class="label" style="left:480px;top:308px"><span class="name">Body Lotion</span><span class="price">$12.00</span></div>
    <div class="label" style="left:471px;top:202px"><span class="name">Body Butter</span><span class="price">$15.00</span></div>
  </section>

  <section class="page page-6">
    <header class="page-header right">
      <span class="page-number">6</span>
      <h2>Pre-Made Collection</h2>
      <svg class="bubble-tail" viewBox="0 0 22 16" style="right:-2px"><path d="M0 0 L22 0 L20 16 Z" fill="#e34297"/></svg>
    </header>

    <div class="product-photo" style="left:623px;top:76px;background:linear-gradient(135deg,#3f5eb0,#7fd2c2 60%,#334f9e)" role="img" aria-label="Wrapped comet bath fizz"></div>
    <div class="product-photo" style="left:769px;top:138px;background:linear-gradient(135deg,#c94a8e,#efe6c8 50%,#b53f80)" role="img" aria-label="Shea butter soaps with coloured hearts"></div>
    <div class="product-photo" style="left:846px;top:250px;background:linear-gradient(135deg,#e052a3,#d23d92)" role="img" aria-label="Bottle of anti bacterial hand gel"></div>
    <div class="product-photo" style="left:969px;top:76px;background:linear-gradient(135deg,#f2f2f4,#c9c7d6 50%,#e9b5a0)" role="img" aria-label="Spray bottle of bug spray beside soaps"></div>

    <div class="label" style="left:695px;top:205px"><span class="name">Comet Bath Fizz w/</span><span class="name">Surprise Inside</span><span class="price">$6.50</span></div>
    <div class="label" style="left:794px;top:270px"><span class="name">Shea Butter</span><span class="name">Heart Soaps</span><span class="price">$3.50</span></div>
    <div class="label" style="left:1061px;top:205px"><span class="name">All-Natural</span><span class="name">Bug Spray</span><span class="price">$7.00</span></div>
    <div class="label" style="left:1067px;top:310px"><span class="name">Anti Bacterial</span><span class="name">Hand Gel</span><span class="price">$3.00</span></div>
  </section>

  <div class="fold-band"></div>
</main>
</body>
</html>
```